New Flyer Design Project

Please see attached word Document

Target Market(s)

Property Investors, home owners

Requirements
Must have
• whats detailed in attached word document

```html
<!DOCTYPE html>
<html lang="en">
<head>
<meta charset="utf-8">
<title>Sound Home Loans Flyer</title>
<link rel="stylesheet" href="https://fonts.googleapis.com/css2?family=Oswald:wght@400;500&family=Arimo:ital,wght@0,400;0,700;1,400&display=swap">
<style>
:root{
  --stage:#7f7f7f;
  --black:#111111;
  --white:#ffffff;
  --red:#e0222a;
  --red-dark:#b5151c;
  --ink:#1c1c1c;
  --navy:#1f3a6b;
  --grey-text:#cfcfcf;
}
*{margin:0;padding:0;box-sizing:border-box}
html,body{width:1200px;height:922px;overflow:hidden;background:var(--stage)}
.canvas{position:relative;width:1200px;height:922px}
.page{position:absolute;top:27px;height:776px;background:var(--white);overflow:hidden}
.page--front{left:40px;width:550px}
.page--back{left:609px;width:549px}
.top-band{position:absolute;z-index:3;left:0;top:0;width:100%;height:35px;background:var(--black);color:var(--white);font:400 21px/35px 'Oswald',sans-serif;text-align:center}
.legal-band{position:absolute;left:0;bottom:0;width:100%;height:36px;background:var(--black);color:var(--grey-text);font:400 9px/36px 'Arimo',sans-serif;text-align:center}

/* front */
.corner{position:absolute;left:0;top:35px}
.corner-text{position:absolute;z-index:2;left:-18px;top:113px;width:260px;height:62px;transform:rotate(-45deg);transform-origin:50% 50%;color:var(--white);font-family:'Oswald',sans-serif;white-space:nowrap;text-align:center}
.corner-phone{font-size:31px;line-height:34px;font-weight:500}
.corner-web{font-size:20px;line-height:28px}
.brand{position:absolute;text-align:center}
.brand-name{display:inline-flex;align-items:center;gap:9px;font:500 30px/1 'Oswald',sans-serif;color:var(--ink);letter-spacing:1px;white-space:nowrap}
.brand-mark{width:18px;height:18px;background:var(--red)}
.brand-tag{font:italic 400 13px/1.5 'Arimo',sans-serif;color:var(--ink);letter-spacing:.5px;white-space:nowrap}
.page--front .brand{left:258px;top:188px;width:280px}
.headline-box{position:absolute;left:0;top:258px;width:533px;height:279px;background:linear-gradient(90deg,#3a3a3a 0,#111 30%,#000 100%)}
.headline{position:absolute;right:32px;top:18px;text-align:right;font:400 77px/82px 'Oswald',sans-serif;color:var(--white);white-space:nowrap}
.headline .accent{color:var(--red);display:block;font-size:86px;line-height:96px}
.lenders-band{position:absolute;left:0;top:543px;width:533px;height:35px;background:linear-gradient(90deg,var(--red) 0,var(--red) 70%,var(--red-dark) 100%);color:var(--white);font:400 22px/35px 'Oswald',sans-serif;text-align:right;padding-right:38px}
.lenders{position:absolute;left:38px;top:590px;width:474px}
.lender-row{display:flex;justify-content:space-between;align-items:center;height:50px}
.lender{display:flex;align-items:center;gap:4px;font:700 11px/1 'Arimo',sans-serif;color:var(--navy);white-space:nowrap}
.lender::before{content:"";width:8px;height:8px;background:var(--red)}

/* back */
.page--back .brand{left:18px;top:52px;text-align:left}
.page--back .brand-name{font-size:31px}
.page--back .brand-tag{padding-left:32px;font-size:12px}
.banner{position:absolute;left:0;top:114px}
.banner-text{position:absolute;left:28px;top:114px;height:46px;font:400 25px/46px 'Oswald',sans-serif;color:var(--white);white-space:nowrap}
.letter{position:absolute;left:11px;top:170px;width:520px;font:400 10px/12px 'Arimo',sans-serif;color:var(--ink);text-align:justify}
.letter p{margin-bottom:11px}
.chart-art{float:left;width:275px;height:180px;margin:0 14px 6px 0;background:linear-gradient(180deg,#ffffff 0,#f1f1f1 45%,#c9c9c9 100%);border-bottom:3px solid var(--red)}
.letter .call{color:var(--red);font-style:italic}
.letter .sign{margin:0}
.letter .sign strong{font-weight:700}
.profile{position:absolute;left:0;top:561px;width:326px;height:142px;background:var(--black)}
.portrait{position:absolute;left:25px;top:8px;width:97px;height:126px;background:linear-gradient(180deg,#e9e9e9,#cfcfcf);border:3px solid var(--white)}
.quals{position:absolute;left:136px;top:9px;color:var(--white);font:400 11px/13px 'Arimo',sans-serif}
.quals h3{font:400 14px/18px 'Oswald',sans-serif;color:var(--red);margin-bottom:3px}
.quals p{margin-bottom:11px}
.money-art{position:absolute;left:331px;top:530px;width:218px;height:184px;background:radial-gradient(ellipse at 50% 60%,#7aa34a 0,#8fb85f 35%,#cfdcbf 62%,#ffffff 78%)}
.contact-band{position:absolute;left:0;top:718px;width:100%;height:32px;background:linear-gradient(90deg,var(--red-dark),var(--red) 40%,var(--red));display:flex;align-items:center;color:var(--white);font:400 13px/1 'Oswald',sans-serif;white-space:nowrap}
.contact-item{display:flex;align-items:center;gap:7px;padding:0 20px;height:22px}
.contact-item + .contact-item{border-left:1px solid rgba(255,255,255,.8)}
.contact-item:first-child{padding-left:40px;width:139px}
.contact-item:nth-child(2){width:218px;justify-content:center}
.contact-item svg{flex:none}
.page--back .legal-band{height:26px;line-height:26px}
</style>
</head>
<body>
<div class="canvas">

  <section class="page page--front">
    <header class="top-band">Keeping the Mortgages of the North West in Good Shape</header>

    <svg class="corner" width="360" height="350" viewBox="0 0 360 350" aria-hidden="true">
      <polygon points="0,0 306,0 0,306" fill="#e0222a"/>
      <polygon points="306,0 318,0 0,318 0,306" fill="#ffffff"/>
      <polygon points="318,0 324,0 0,324 0,318" fill="#e0222a"/>
    </svg>
    <div class="corner-text">
      <div class="corner-phone">1300 555 018</div>
      <div class="corner-web">www.soundhomeloans.com.au</div>
    </div>

    <div class="brand">
      <div class="brand-name"><span class="brand-mark"></span>SOUND HOME LOANS</div>
      <div class="brand-tag">Is your mortgage in good shape?</div>
    </div>

    <div class="headline-box">
      <h1 class="headline">IS YOUR<br>MORTGAGE IN<span class="accent">GOOD SHAPE</span></h1>
    </div>

    <div class="lenders-band">WE ASSESS OVER 30 LENDERS</div>

    <div class="lenders">
      <div class="lender-row">
        <span class="lender">Orbit</span><span class="lender">Larch</span><span class="lender">Pinecrest</span><span class="lender">Meridian</span><span class="lender">Coastal</span><span class="lender">Summit</span><span class="lender">Bluewater</span>
      </div>
      <div class="lender-row">
        <span class="lender">Redgum</span><span class="lender">Northgate</span><span class="lender">Cobalt</span><span class="lender">Keystone</span><span class="lender">Peak</span><span class="lender">Lantern</span><span class="lender">Greenleaf</span>
      </div>
      <div class="lender-row">
        <span class="lender">Banksia</span><span class="lender">Goldline</span><span class="lender">Southern</span><span class="lender">Arrow</span><span class="lender">Starline</span><span class="lender">Horizon</span>
      </div>
    </div>

    <footer class="legal-band">Sound Home Loans ABN 12 345 678 901 ACR No. 100200 is a credit representative of Ridgeline Credit ACL No 300400</footer>
  </section>

  <section class="page page--back">
    <header class="top-band">Cutting out the Fatty Commissions</header>

    <div class="brand">
      <div class="brand-name"><span class="brand-mark"></span>SOUND HOME LOANS</div>
      <div class="brand-tag">Is your mortgage in good shape?</div>
    </div>

    <svg class="banner" width="460" height="46" viewBox="0 0 460 46" aria-hidden="true">
      <defs>
        <linearGradient id="bannerFill" x1="0" x2="1" y1="0" y2="0">
          <stop offset="0" stop-color="#d91c24"/>
          <stop offset="1" stop-color="#b5151c"/>
        </linearGradient>
      </defs>
      <polygon points="0,0 430,0 455,23 430,46 0,46" fill="url(#bannerFill)"/>
    </svg>
    <h2 class="banner-text">INVESTMENT PROPERTY SPECIALISTS’</h2>

    <article class="letter">
      <div class="chart-art" role="img" aria-label="Illustration of houses growing taller along a rising red arrow"></div>
      <p>Hi, my names Daniel Ashford founder of Sound Home Loans. In 2014 whilst serving in the forces on an average wage, I purchased 7 properties across two states, these properties are now paying for themselves, and have all grown in value.</p>
      <p>I am not sharing this to gloat, but to express to you the opportunities that are open to even those on average or low wages. I now specialise in assisting middle and low income earners obtain property portfolios which can set themselves and their families up for a comfortable, and in many cases, early retirement.</p>
      <p>As a Professional Broker I assist client’s structure their property portfolio to ensure it is positioned to expand into the future. Although, my true value resides within my intimate knowledge of property markets across the country, which has been developed through 1000’s of hours of research from personal investing.</p>
      <p>Best of all, you will have my added investment knowledge free of charge. My only payment is funded by the banks should you purchase a property and allow me to broker your loan.</p>
      <p>Furthermore, Sound Home Loans does not accept any commission or kickbacks from developers or agents. However, please be wary as the Investment Property Industry is currently unregulated, with many so called experts flashing nice brochures and big seminars to lead you to their commission packed properties, and these commissions can be in excess of $30,000. At your expense!!</p>
      <p class="call">So if you are after some guidance on how to get started, or looking at expanding your current portfolio. Please contact me for some honest and transparent advice.</p>
      <p class="sign">Happy Investing!!<br><strong>Daniel Ashford</strong></p>
    </article>

    <div class="profile">
      <div class="portrait" role="img" aria-label="Portrait photo of the broker"></div>
      <div class="quals">
        <h3>PROFESSIONAL QUALIFICATIONS</h3>
        <p>Bachelor of Accounting</p>
        <p>Diploma in Finance<br>-Mortgage Broker</p>
        <p>Broker Association member</p>
      </div>
    </div>

    <div class="money-art" role="img" aria-label="Photo of a house built from stacks of banknotes"></div>

    <div class="contact-band">
      <span class="contact-item">1300 555 018</span>
      <span class="contact-item">
        <svg width="15" height="11" viewBox="0 0 15 11" aria-hidden="true"><rect x=".5" y=".5" width="14" height="10" fill="none" stroke="#fff"/><polyline points=".5,.5 7.5,6 14.5,.5" fill="none" stroke="#fff"/></svg>
        daniel@soundhomeloans.com.au
      </span>
      <span class="contact-item">
        <svg width="14" height="14" viewBox="0 0 14 14" aria-hidden="true"><circle cx="7" cy="7" r="6.2" fill="none" stroke="#fff" stroke-width="1.2"/><ellipse cx="7" cy="7" rx="2.8" ry="6.2" fill="none" stroke="#fff"/><line x1=".8" y1="7" x2="13.2" y2="7" stroke="#fff"/></svg>
        www.soundhomeloans.com.au
      </span>
    </div>

    <footer class="legal-band">Sound Home Loans ABN 12 345 678 901 ACR No. 100200 is a credit representative of Ridgeline Credit ACL No 300400</footer>
  </section>

</div>
</body>
</html>
```